Business Card - high end, modern health care

Hey designers!

We need a double sided business card for the boutique, cutting edge physical therapy rehabilitation centre in Sydney's Northern Beaches.

With the most qualified physios in the area The Harbourview Motion Clinic does what other physiotherapy practices do not, we take our time with our patients giving them longer appointments, better physios and therefor faster results!

We guarantee that the service people receive at THMC will be unparalleled.

Hence we need a business card to reflect our modern, boutique, high end service. The final design needs to reflect that we are in a class of our own yet with the feel of beachside retreat.

Below I have attached our logo in both blue on white and white on blue. The exact colour is;
and the font that we have used in our logo is Tex Gyre Aventador.

I like the idea of the blue as the main colour as it is more eye catching and our signage onto the main road will be in this blue and in the interest of consistency across marketing the blue needs to be a part of the design. However I would appreciate a few designs onto a wooden background as this is a visual theme within the fitout of the practice.

The design needs to be of standard size (91x55mm).

Target Market(s)

We target people who have an end outcome in mind and those who have had poor experiences with other providers and ensure that everyone gets the care that they deserve with a premium service that is tailored to the individuals circumstances. As a premium service, the target market is highly educated, business and tech savvy with the additional target market of elderly people who have self funded their retirement and see value in paying for the best ongoing rehabilitation to maintain independence.

Industry/Entity Type

Physical Therapy

Contact Information for Business Card

Name, designation( Titled Musculoskeletal Physiotherapist... there will also be those in the company that have multiple designations ie 5 or 6 words long), phone number, email, facebook, instagram, address

Font styles to use
Sans Serif

Colors

Designer to choose colors to be used in the design.

Requirements
Must have
• Front - The logo as large as possible, blue or wooden theme, and all of the important details.
• Back - A blank space/lines on which to write appointment times (no "Appointment, date, time" etc.)
Nice to have
• facebook url
• logos for facebook and instagram
• Mini logos for the phone and email?

```html
<!DOCTYPE html>
<html lang="en">
<head>
<meta charset="utf-8">
<title>The Harbourview Motion Clinic – Business Card</title>
<link href="https://fonts.googleapis.com/css2?family=Lato:wght@400;700&display=swap" rel="stylesheet">
<style>
  :root {
    --brand-blue: #0b57a8;
    --band-grey: #e3e3e3;
    --wave-grey: #8a8a8a;
    --ink-grey: #3d3d3d;
    --paper: #ffffff;
    --backdrop: #efece7;
  }
  * { box-sizing: border-box; margin: 0; padding: 0; }
  html, body { width: 1200px; height: 900px; overflow: hidden; }
  body {
    background: var(--backdrop);
    font-family: "Lato", Arial, sans-serif;
    position: relative;
  }
  .card {
    position: absolute;
    top: 290px;
    width: 530px;
    height: 320px;
    overflow: hidden;
    box-shadow: 0 6px 18px rgba(0,0,0,0.18);
  }
  /* ---------- back (appointment) ---------- */
  .card--back { left: 45px; background: var(--brand-blue); }
  .back-logo {
    position: absolute;
    left: 70px; top: 62px;
    display: flex; align-items: center; gap: 14px;
    color: var(--paper);
  }
  .logo-disc {
    width: 68px; height: 68px; border-radius: 50%;
    background: var(--paper); flex: none;
  }
  .logo-name {
    font-weight: 700;
    text-transform: uppercase;
    line-height: 1.05;
    letter-spacing: 0.5px;
  }
  .back-logo .logo-name { font-size: 30px; }
  .appointment-band {
    position: absolute;
    left: 0; right: 0; top: 180px; height: 96px;
    background: var(--band-grey);
  }
  .appointment-row {
    position: absolute;
    left: 70px; right: 40px;
    display: flex; align-items: flex-end; gap: 6px;
    color: var(--brand-blue);
    font-size: 14px; font-weight: 700; letter-spacing: 0.5px;
  }
  .appointment-row--top { top: 12px; }
  .appointment-row--bottom { top: 56px; }
  .write-line { flex: 1; border-bottom: 1px solid var(--brand-blue); height: 14px; }
  .write-line--short { flex: 0 0 130px; }
  /* ---------- front (contact) ---------- */
  .card--front { left: 625px; background: var(--paper); }
  .card-wave { position: absolute; left: 0; top: 0; }
  .holder {
    position: absolute; left: 40px; top: 64px;
  }
  .holder-name {
    color: var(--brand-blue);
    font-size: 21px; font-weight: 700; letter-spacing: 0.3px;
    text-transform: uppercase;
  }
  .holder-title { color: var(--ink-grey); font-size: 15px; margin-top: 1px; }
  .front-logo {
    position: absolute; right: 26px; top: 28px;
    display: flex; flex-direction: column; align-items: center; gap: 12px;
    width: 200px;
  }
  .front-logo .logo-disc {
    width: 116px; height: 116px; background: var(--brand-blue);
  }
  .front-logo .logo-name {
    color: var(--brand-blue); font-size: 17px; text-align: center;
  }
  .contact-list {
    position: absolute; left: 40px; top: 186px;
    list-style: none;
    color: var(--ink-grey); font-size: 15px;
  }
  .contact-list li { display: flex; align-items: center; gap: 7px; height: 20px; }
  .contact-list li.gap-before { margin-top: 8px; }
  .contact-icon { width: 16px; height: 16px; flex: none; }
  .social-dot {
    width: 16px; height: 16px; border-radius: 50%;
    background: var(--brand-blue); flex: none;
  }
</style>
</head>
<body>

  <section class="card card--back" aria-label="Appointment side">
    <div class="back-logo">
      <span class="logo-disc"></span>
      <span class="logo-name">The Harbourview<br>Motion Clinic</span>
    </div>
    <div class="appointment-band">
      <div class="appointment-row appointment-row--top">
        <span class="write-line"></span><span>TIME</span><span class="write-line write-line--short"></span>
      </div>
      <div class="appointment-row appointment-row--bottom">
        <span>DATE</span><span class="write-line"></span>
      </div>
    </div>
  </section>

  <section class="card card--front" aria-label="Contact side">
    <svg class="card-wave" width="530" height="320" viewBox="0 0 530 320" aria-hidden="true">
      <path d="M530,196 C420,196 340,248 250,284 C170,314 80,306 0,286 L0,320 L530,320 Z" fill="var(--wave-grey)"/>
      <path d="M530,190 C430,196 360,250 270,290 C200,318 100,318 0,300 L0,320 L530,320 Z" fill="var(--paper)"/>
      <path d="M530,186 C440,192 370,252 280,294 C210,322 100,324 0,306 L0,320 L530,320 Z" fill="var(--brand-blue)"/>
    </svg>

    <div class="holder">
      <p class="holder-name">Daniel Carver</p>
      <p class="holder-title">Managing Director</p>
    </div>

    <div class="front-logo">
      <span class="logo-disc"></span>
      <span class="logo-name">The Harbourview<br>Motion Clinic</span>
    </div>

    <ul class="contact-list">
      <li>
        <svg class="contact-icon" viewBox="0 0 16 16" aria-hidden="true">
          <circle cx="8" cy="8" r="7.2" fill="none" stroke="var(--brand-blue)" stroke-width="1.4"/>
          <path d="M5.6 4.4 L6.8 4.2 L7.4 6 L6.6 6.7 C7 7.8 8.1 8.9 9.2 9.3 L9.9 8.5 L11.7 9.1 L11.5 10.3 C8.2 10.8 5 7.7 5.6 4.4 Z" fill="var(--brand-blue)"/>
        </svg>
        444 555 0199
      </li>
      <li>
        <svg class="contact-icon" viewBox="0 0 16 16" aria-hidden="true">
          <circle cx="8" cy="8" r="8" fill="var(--brand-blue)"/>
          <rect x="4" y="5.2" width="8" height="5.6" fill="none" stroke="#fff" stroke-width="1"/>
          <path d="M4 5.4 L8 8.4 L12 5.4" fill="none" stroke="#fff" stroke-width="1"/>
        </svg>
        info@harbourviewmotion.com
      </li>
      <li class="gap-before"><span class="social-dot"></span>/harbourviewmotionclinic</li>
      <li><span class="social-dot"></span>@harbourviewmotionclinic</li>
    </ul>
  </section>

</body>
</html>
```